Kellwyn Surface Records

I have a current web site that it looking quite aged and it needs a new lease of life. This is a Graffiti Management Website so is all about data processing and management of information. I want a html 5 view on any platform design. clean crisp and new. I have provided some screen shots of my current site.

Target Market(s)

The Target Market will be local government. most users will not be heavy pc users

Industry/Entity Type

Management

Font styles to use
Sans Serif
Other font styles liked:
• web font like calibri

Colors

Designer to choose colors to be used in the design.

Requirements
Must have
• Must have menus similar to attachments

```html
<!DOCTYPE html>
<html lang="en">
<head>
<meta charset="utf-8">
<title>KSR – Kellwyn Surface Records</title>
<link href="https://fonts.googleapis.com/css2?family=Mulish:ital,wght@0,400;0,600;0,700;1,600;1,700&display=swap" rel="stylesheet">
<style>
:root{
  --navy:#0b1a3a;
  --blue:#0d4ab0;
  --blue-dark:#0b3e96;
  --sky:#6aa6dc;
  --sky-light:#8fc0ea;
  --red:#c90c12;
  --red-text:#d42a1e;
  --card:#f4f4f4;
  --text:#444;
  --white:#fff;
  --dark:#2b2b2b;
}
*{margin:0;padding:0;box-sizing:border-box}
html,body{width:858px;height:1200px;overflow:hidden;background:var(--white)}
body{position:relative;font-family:"Mulish",sans-serif;color:var(--text)}
.topline{position:absolute;left:0;top:0;width:858px;height:2px;background:var(--dark)}
.account{position:absolute;left:677px;top:2px;width:128px;height:22px;background:var(--dark);color:var(--white);font-size:8px;display:flex;align-items:center;justify-content:center;gap:7px;letter-spacing:.2px}
.header{position:absolute;left:0;top:32px;width:858px;height:78px;
  background:repeating-linear-gradient(180deg,var(--sky) 0 2px,var(--sky-light) 2px 4px)}
.header .stripe{position:absolute;left:0;top:46px;width:858px;height:10px;background:var(--navy);border-top:2px solid var(--white)}
.brand{position:absolute;left:69px;top:14px;color:var(--white);font-weight:700;font-size:25px;letter-spacing:15px;line-height:1}
.brand-sub{position:absolute;left:69px;top:48px;color:var(--white);font-weight:700;font-size:8px;letter-spacing:1.4px}
.tagline{position:absolute;right:53px;top:8px;color:var(--white);font-style:italic;font-weight:600;font-size:17px}
.nav{position:absolute;left:328px;top:32px;width:477px;height:34px;background:var(--blue);
  clip-path:polygon(8px 0,100% 0,100% 100%,0 100%);display:flex;align-items:center;justify-content:space-around;padding-left:10px}
.nav a{color:var(--white);font-size:8.5px;text-decoration:none;letter-spacing:.3px}
.hero{position:absolute;left:0;top:110px;width:858px;height:274px;
  background:radial-gradient(ellipse at 62% 40%,#1d5d9c 0%,#0e2c55 40%,#08162e 80%)}
.hero-title{position:absolute;left:53px;top:64px;width:340px;color:var(--white);font-style:italic;font-weight:700;font-size:19.5px;line-height:26.5px}
.btn{position:absolute;left:53px;top:160px;width:109px;height:28px;background:var(--red);color:var(--white);font-style:italic;font-weight:700;font-size:12.5px;display:flex;align-items:center;justify-content:center}
.dots{position:absolute;left:53px;top:237px;display:flex;gap:3px}
.dots span{width:9px;height:9px;border-radius:50%;background:var(--white)}
.dots span.on{background:var(--blue)}
h2{font-weight:600;font-size:15.5px;text-align:center;letter-spacing:.3px}
.welcome{position:absolute;left:0;top:384px;width:858px;height:130px}
.welcome h2{color:var(--blue);margin-top:24px}
.welcome p{width:750px;margin:10px auto 0;font-size:8.4px;line-height:15.2px;text-align:center}
.products{position:absolute;left:0;top:514px;width:858px;height:292px;background:var(--red)}
.products h2{color:var(--white);margin-top:20px}
.grid{position:absolute;left:53px;top:50px;display:grid;grid-template-columns:repeat(3,236px);column-gap:22px;row-gap:17px}
.card{height:98px;background:var(--card);padding:11px 10px;box-shadow:0 2px 2px rgba(0,0,0,.35)}
.card h3{color:var(--blue);font-weight:600;font-size:10px;margin-bottom:2px}
.card p{font-size:8.3px;line-height:15.2px}
.benefits{position:absolute;left:0;top:806px;width:858px;height:302px}
.benefits h2{color:var(--blue);margin-top:32px}
.bgrid{position:absolute;left:53px;top:69px;display:grid;grid-template-columns:repeat(4,174px);column-gap:19px}
.photo{width:174px;height:101px}
.benefit h3{color:var(--red-text);font-weight:600;font-size:10px;margin:12px 0 2px}
.benefit p{font-size:8.4px;line-height:15.2px}
.footer{position:absolute;left:0;top:1108px;width:858px;height:92px;background:var(--blue)}
.flinks{position:absolute;left:53px;top:21px;color:var(--white);font-size:8px;letter-spacing:.2px}
.flinks span{margin:0 5px}
.copy{position:absolute;left:53px;top:57px;color:var(--white);font-size:8px}
.connect{position:absolute;left:726px;top:18px;color:var(--white);font-size:8.5px}
.social{position:absolute;left:726px;top:36px;display:flex;gap:7px}
.social span{width:22px;height:22px;border-radius:50%;background:#3d7fd8;border:1px solid #9cc4f2}
</style>
</head>
<body>
<div class="topline"></div>
<div class="account"><span>LOG IN</span><span>|</span><span>DEMO LOG IN</span></div>

<header class="header">
  <div class="stripe"></div>
  <div class="brand">KSR</div>
  <div class="brand-sub">KELLWYN SURFACE RECORDS</div>
  <div class="tagline">Helping You Clean Up Your Community</div>
  <nav class="nav">
    <a>HOME</a><a>PRODUCTS</a><a>REPORTS</a><a>BENEFITS</a><a>LEGISLATION</a><a>CONTACT US</a>
  </nav>
</header>

<section class="hero" role="img" aria-label="Hand touching a glowing digital technology interface">
  <h1 class="hero-title">KSR is an Online Database System to Manage Graffiti in your area or Your Properties..</h1>
  <div class="btn">Read More &gt;&gt;</div>
  <div class="dots"><span class="on"></span><span></span><span></span><span></span></div>
</section>

<section class="welcome">
  <h2>WELCOME TO OUR WEBSITE</h2>
  <p>KSR is an Online Database System to Manage Graffiti in your area or Your Properties. KSR allows you to Register, Track, Report and Archive Graffiti Jobs with Photographic Records. KSR records both Estimated and Actual hours and costs for each job, enabling you to track the effectiveness of Anti Graffiti policy. KSR allows sharing of Critical Graffiti Tag and Photographic Data between its subscribers, assisting with tracking down Serial Graffiti Offenders. KSR has a Statistical and Comparison Reporting Systems to allow its subscribers to graphically report and compare their Graffiti Data.</p>
</section>

<section class="products">
  <h2>OUR PRODUCTS</h2>
  <div class="grid">
    <div class="card"><h3>GRAFFITI REGISTER</h3><p>KSR provides a National Register of Vandalism and Graffiti. Subscribers to the KSR Database can Add, Change, Report on and Archive their own Graffiti Jobs...</p></div>
    <div class="card"><h3>GRAFFITI PHOTOS</h3><p>KSR provides a National Register of Vandalism and Graffiti. Subscribers to the KSR Database can Add, Change, Report on and Archive their own Graffiti Jobs...</p></div>
    <div class="card"><h3>GRAFFITI ARCHIVE</h3><p>KSR provides a National Register of Vandalism and Graffiti. Subscribers to the KSR Database can Add, Change, Report on and Archive their own Graffiti Jobs...</p></div>
    <div class="card"><h3>SEARCHABLE DATABASE</h3><p>KSR provides a National Register of Vandalism and Graffiti. Subscribers to the KSR Database can Add, Change, Report on and Archive their own Graffiti Jobs...</p></div>
    <div class="card"><h3>STATISITCAL ANALYSIS REPORTS</h3><p>KSR provides a National Register of Vandalism and Graffiti. Subscribers to the KSR Database can Add, Change, Report on and Archive their own Graffiti Jobs...</p></div>
    <div class="card"><h3>DATA CONVERSION</h3><p>KSR provides a National Register of Vandalism and Graffiti. Subscribers to the KSR Database can Add, Change, Report on and Archive their own Graffiti Jobs...</p></div>
  </div>
</section>

<section class="benefits">
  <h2>BENEFITS</h2>
  <div class="bgrid">
    <div class="benefit">
      <div class="photo" role="img" aria-label="Calculator and pen on printed blue financial charts" style="background:linear-gradient(135deg,#dfe9f5,#4f8fd6)"></div>
      <h3>COST EFFECTIVE</h3>
      <p>KSR allows you to track the cost and effectiveness of your Graffiti Removal. Compare the estimates and actual costs for External Contractors against inhouse removal.</p>
    </div>
    <div class="benefit">
      <div class="photo" role="img" aria-label="Close-up of a camera lens held in a hand" style="background:linear-gradient(135deg,#8a8a8a,#1e1e1e)"></div>
      <h3>PHOTOGRAPHIC RECORDS</h3>
      <p>KSR allows you to track the cost and effectiveness of your Graffiti Removal. Compare the estimates and actual costs for External Contractors against inhouse removal.</p>
    </div>
    <div class="benefit">
      <div class="photo" role="img" aria-label="Judge's gavel beside a hand signing a document" style="background:linear-gradient(135deg,#5a4a2e,#d8cfc0)"></div>
      <h3>ASSIST PROSECUTION</h3>
      <p>KSR allows you to track the cost and effectiveness of your Graffiti Removal. Compare the estimates and actual costs for External Contractors against inhouse removal.</p>
    </div>
    <div class="benefit">
      <div class="photo" role="img" aria-label="Finger on a glowing fingerprint security interface" style="background:radial-gradient(circle at 60% 55%,#2a6fa8,#0b2038)"></div>
      <h3>ACCESS AND SECURITY</h3>
      <p>KSR allows you to track the cost and effectiveness of your Graffiti Removal. Compare the estimates and actual costs for External Contractors against inhouse removal.</p>
    </div>
  </div>
</section>

<footer class="footer">
  <div class="flinks">HOME<span>/</span>PRODUCTS<span>/</span>REPORTS<span>/</span>BENEFITS<span>/</span>LEGISLATION<span>/</span>CONTACT US</div>
  <div class="copy">COPYRIGHT © 2014. KSR. ALL RIGHT RESERVED</div>
  <div class="connect">CONNECT US:</div>
  <div class="social"><span></span><span></span><span></span></div>
</footer>
</body>
</html>
```